Business Card Design needed for start up company Halvora

In need of a new business card designed for a start up company based in Sydney, Halvora is a new start up innovative Company, our mission it to make property accessible for everyday Australian and to become the leading Real Estate platform in Australia. We want it to be fresh and clean.

Industry/Entity Type

Financial

Contact Information for Business Card

Section for Name
Section for Title

HALVORA - The Strength of Pooling
Mobile:
Direct:

Font styles to use
Sans Serif

Colors
33a6d7
0692cd
0255a3
ffffff

Requirements
Must have
• Logo, all business card details

```html
<!DOCTYPE html>
<html lang="en">
<head>
<meta charset="utf-8">
<title>Halvora — Business Card</title>
<link rel="stylesheet" href="https://fonts.googleapis.com/css2?family=Open+Sans:wght@400;600;800&display=swap">
<style>
  :root {
    --backdrop: #1c1c1d;
    --card: #2a2a2b;
    --card-edge: #323233;
    --sky: #4fbbe9;
    --brand-blue: #0255a3;
    --azure: #33a6d7;
    --white: #ffffff;
    --text-soft: #d6d6d6;
    --front-mark: #5a5a5b;
    --front-word: #bdbdbd;
  }
  * { box-sizing: border-box; margin: 0; padding: 0; }
  html, body {
    width: 1200px; height: 1000px; overflow: hidden;
    background: var(--backdrop);
    font-family: "Open Sans", Arial, sans-serif;
  }
  .card {
    position: absolute; left: 220px;
    width: 760px; height: 434px;
    background: var(--card);
    border: 1px solid var(--card-edge);
    border-radius: 4px;
  }
  .card--front { top: 38px; display: flex; align-items: center; justify-content: center; }
  .card--back { top: 520px; }

  .brand { display: flex; align-items: center; gap: 14px; white-space: nowrap; }
  .brand__dot { width: 80px; height: 80px; border-radius: 50%; flex: none; }
  .brand__name { font-weight: 800; font-size: 56px; letter-spacing: 0.5px; line-height: 1; }
  .card--front .brand__dot { background: var(--front-mark); }
  .card--front .brand__name { color: var(--front-word); }

  .card--back .brand { position: absolute; left: 60px; top: 184px; gap: 12px; }
  .card--back .brand__dot { width: 66px; height: 66px; background: var(--sky); }
  .card--back .brand__name { color: var(--brand-blue); font-size: 44px; letter-spacing: 0; }

  .divider {
    position: absolute; left: 408px; top: 110px;
    width: 2px; height: 214px; background: var(--white);
  }
  .contact { position: absolute; left: 436px; top: 104px; color: var(--text-soft); }
  .contact__name { color: var(--sky); font-weight: 600; font-size: 26px; letter-spacing: 1px; line-height: 1.1; }
  .contact__title { color: var(--white); font-weight: 600; font-size: 17px; letter-spacing: 1px; margin-bottom: 10px; }
  .contact__address { font-size: 16px; letter-spacing: 1px; line-height: 1.3; margin-bottom: 10px; }
  .contact__list { list-style: none; }
  .contact__item { display: flex; align-items: center; gap: 14px; font-size: 17px; letter-spacing: 0.8px; height: 26px; white-space: nowrap; }
  .contact__icon {
    width: 18px; height: 18px; border-radius: 50%; background: var(--sky);
    display: flex; align-items: center; justify-content: center; flex: none;
  }
  .contact__icon svg { width: 11px; height: 11px; }
  .contact__web-accent { color: var(--azure); }
</style>
</head>
<body>
  <section class="card card--front" aria-label="Card front">
    <div class="brand">
      <span class="brand__dot"></span>
      <span class="brand__name">HALVORA</span>
    </div>
  </section>

  <section class="card card--back" aria-label="Card back">
    <div class="brand">
      <span class="brand__dot"></span>
      <span class="brand__name">HALVORA</span>
    </div>
    <div class="divider"></div>
    <div class="contact">
      <p class="contact__name">Elena Marsh</p>
      <p class="contact__title">Director</p>
      <p class="contact__address">Your Street Address,<br>Sydney, 1234</p>
      <ul class="contact__list">
        <li class="contact__item">
          <span class="contact__icon"><svg viewBox="0 0 12 12"><path d="M2.5 1.5l2 .3.6 2.2-1.2.9a6 6 0 0 0 3.2 3.2l.9-1.2 2.2.6.3 2A1.2 1.2 0 0 1 9.3 10.7 8.5 8.5 0 0 1 1.3 2.7 1.2 1.2 0 0 1 2.5 1.5z" fill="#fff"/></svg></span>
          000 123 456 789
        </li>
        <li class="contact__item">
          <span class="contact__icon"><svg viewBox="0 0 12 12"><rect x="3.5" y="1" width="5" height="10" rx="1" fill="none" stroke="#fff" stroke-width="1.2"/></svg></span>
          000 222 3334
        </li>
        <li class="contact__item">
          <span class="contact__icon"><svg viewBox="0 0 12 12"><rect x="1.5" y="3" width="9" height="6" fill="none" stroke="#fff" stroke-width="1.1"/><path d="M1.5 3l4.5 3.5L10.5 3" fill="none" stroke="#fff" stroke-width="1.1"/></svg></span>
          urname@email.com
        </li>
        <li class="contact__item">
          <span class="contact__icon"><svg viewBox="0 0 12 12"><circle cx="6" cy="6" r="4.5" fill="none" stroke="#fff" stroke-width="1"/><ellipse cx="6" cy="6" rx="2" ry="4.5" fill="none" stroke="#fff" stroke-width="1"/><path d="M1.5 6h9" stroke="#fff" stroke-width="1"/></svg></span>
          <span>www.<span class="contact__web-accent">websitename</span>.com</span>
        </li>
      </ul>
    </div>
  </section>
</body>
</html>
```